New Website Design & Build Project - Lively Oak Dishes

I am looking for a professional clean looking website design then build of a website for my meal delivery business Lively Oak Dishes. I already have the domain - www.livelyoakdishes.com.au and I will upload brief for the design and layout of the website.

I have a dropbox full of photos, designs, videos and existing graphic design work that I can share with the designers. This can be provided upon designer request.

I am looking to build this site in WORDPRESS and I would like to build the site using the Velmora Page Composer - https://velmoraskins.example/

Target Market(s)

Kids from 2-16 , Teenagers - 16 - 19, Adults - 19 - 80 + - We Cater For Everyone

Industry/Entity Type

Health And Wellness

Coding

Coded - Design and coding required

Number of Pages Required

5+ page

Colors
33b8a4
abd037
ec1f27
fbee3f
3276b5

Requirements
Must have
• Must incorporate the included Lively Oak Dishes & LOD Logo
Must incorporate designs of packaging into website design.
Must keep text styles consistant throughout design
Must be mobile, tablet and desktop view responsive on all devices.
Must be built in Wordpress
The coder must have experience with velmora skins, velmora page composer, velmora prospects and also be very experienced with setting up products using Quillo Storefront plug in-
https://quillostorefront.example/
I want to integrate Postwren - https://dealbarn.example/postwren/ into site as well
Nice to have
• All of the above
Should not have
• No dark colours

```html
<!DOCTYPE html>
<html lang="en">
<head>
<meta charset="utf-8">
<title>Lively Oak Dishes – Healthy Meals</title>
<link href="https://fonts.googleapis.com/css2?family=Lato:wght@400;700&family=Montserrat:wght@400;500&family=Michroma&display=swap" rel="stylesheet">
<style>
:root{
  --green:#66bb44;
  --blue:#3276b5;
  --navy:#2d5c9e;
  --teal:#33b8a4;
  --red:#ec1f27;
  --ink:#1d1d1d;
  --text:#333;
  --muted:#777;
  --soft-bg:#f5f5f5;
  --footer-bg:#1b1b1b;
  --line:#e3e3e3;
}
*{box-sizing:border-box;margin:0;padding:0}
html,body{width:1200px;height:3301px;overflow:hidden}
body{position:relative;background:#fff;font-family:"Lato",sans-serif;color:var(--text)}
.abs{position:absolute}
.wide{font-family:"Michroma",sans-serif;text-transform:uppercase;letter-spacing:5px}
.btn{position:absolute;display:flex;align-items:center;justify-content:center;color:#fff;font-family:"Lato",sans-serif;font-weight:700;font-size:16px;border-radius:2px}
.ph{position:absolute;border-radius:4px}

/* header */
.site-header{position:absolute;left:0;top:0;width:1200px;height:70px;background:#fff;border-bottom:1px solid #eee}
.brand{position:absolute;left:111px;top:19px;font-weight:700;font-size:26px;color:var(--ink);display:flex;align-items:center;gap:10px}
.brand .dot{width:16px;height:16px;background:var(--green)}
.nav{position:absolute;left:460px;top:24px;display:flex;gap:12px;font-size:16px;color:var(--ink)}
.nav .active{color:var(--green)}
.nav .sep{color:#555}
.login{position:absolute;left:816px;top:24px;font-weight:700;font-size:16px;color:var(--ink);display:flex;gap:6px;align-items:center}
.signup{left:897px;top:14px;width:95px;height:40px;background:var(--green)}

/* hero */
.hero{position:absolute;left:0;top:70px;width:1200px;height:603px;background:linear-gradient(180deg,#f3f3f2,#ebebea)}
.hero-title{left:109px;top:262px;font-size:34px;color:var(--blue);letter-spacing:8px}
.hero-sub{left:110px;top:316px;font-size:20px;color:var(--ink);letter-spacing:.3px}
.hero-btn{left:110px;top:360px;width:177px;height:46px;background:var(--blue)}
.badge{position:absolute;border-radius:50%;color:#fff;font-weight:700;font-size:14px;display:flex;flex-direction:column;align-items:center;justify-content:center;line-height:1.4}
.dots{left:111px;top:576px;display:flex;gap:9px}
.dots span{width:10px;height:10px;border-radius:50%;border:1px solid var(--blue)}
.dots .on{background:var(--blue)}

/* subscribe */
.subscribe{left:110px;top:620px;width:980px;height:165px;background:#fff;border-top:3px solid var(--green);box-shadow:0 2px 10px rgba(0,0,0,.12)}
.subscribe p{position:absolute;left:0;width:980px;top:36px;text-align:center;font-size:20px;color:var(--ink)}
.sub-input{position:absolute;left:269px;top:81px;width:310px;height:48px;border:1px solid #ddd;border-right:0;font-family:"Montserrat",sans-serif;font-size:13px;color:#888;padding:16px 17px}
.sub-btn{left:579px;top:81px;width:130px;height:48px;background:var(--green)}

/* fresh */
.section-title{left:0;width:1200px;text-align:center;font-size:24px;color:var(--ink)}
.rule{height:3px;width:38px;background:var(--green)}
.card{position:absolute;top:933px;width:237px;height:357px;border:1px solid var(--line);background:#fff}
.card .photo{position:absolute;left:4px;top:4px;width:227px;height:174px;border-radius:0}
.card h3{position:absolute;left:0;width:235px;top:194px;text-align:center;font-family:"Montserrat",sans-serif;font-weight:400;font-size:19px;line-height:26px;color:var(--ink)}
.card .price{position:absolute;left:0;width:235px;top:256px;text-align:center;font-family:"Montserrat",sans-serif;font-weight:500;font-size:32px}
.card .btn{left:61px;top:306px;width:113px;height:40px}

/* online ordering */
.ordering{left:0;top:1376px;width:1200px;height:362px;background:linear-gradient(100deg,#4a3f35 0%,#6b5a48 45%,#4d372b 100%)}
.ordering h2{position:absolute;left:0;width:1200px;top:82px;text-align:center;color:#fff;font-size:28px}
.ordering p{position:absolute;left:140px;width:920px;top:128px;text-align:center;color:#fff;font-family:"Montserrat",sans-serif;font-size:14px;line-height:28px}
.ordering .btn{left:478px;top:232px;width:177px;height:46px;background:var(--green)}

/* how it works */
.how{left:0;top:1738px;width:1200px;height:538px;background:var(--soft-bg)}
.step-ring{position:absolute;width:112px;height:112px;border-radius:50%;border:2px solid var(--green);background:#fff}
.step-num{position:absolute;width:26px;height:26px;border-radius:50%;background:var(--navy);color:#fff;font-size:14px;font-weight:700;display:flex;align-items:center;justify-content:center}
.step h4{position:absolute;width:300px;text-align:center;font-size:21px;font-weight:400;color:var(--ink)}
.step p{position:absolute;width:300px;text-align:center;font-family:"Montserrat",sans-serif;font-size:14px;line-height:25px;color:var(--muted)}

/* smoothie */
.smoothie-brand{left:111px;top:2358px;font-weight:700;font-size:30px;color:var(--ink);display:flex;gap:10px;align-items:center}
.smoothie-brand .dot{width:18px;height:18px;background:var(--green)}
.smoothie h2{position:absolute;left:111px;top:2418px;font-size:22px;line-height:31px;color:var(--green);letter-spacing:6px}
.smoothie p{position:absolute;left:113px;width:485px;font-family:"Montserrat",sans-serif;font-size:13.4px;line-height:28.3px;color:var(--muted)}

/* footer */
.site-footer{left:0;top:2946px;width:1200px;height:355px;background:var(--footer-bg);color:#fff}
.site-footer h5{position:absolute;font-weight:700;font-size:16px;letter-spacing:.5px}
.site-footer ul{position:absolute;list-style:none;font-family:"Montserrat",sans-serif;font-size:14px;line-height:28px}
.social{position:absolute;width:38px;height:38px;border-radius:50%;border:2px solid #fff}
.legal{position:absolute;left:0;width:1200px;text-align:center;font-family:"Montserrat",sans-serif;font-size:14px}
</style>
</head>
<body>

<header class="site-header">
  <div class="brand"><span class="dot"></span>Lively Oak Dishes</div>
  <nav class="nav">
    <span class="active">Our menu</span><span class="sep">|</span>
    <span>About us</span><span class="sep">|</span>
    <span>Blog</span><span class="sep">|</span>
    <span>Contact us</span>
  </nav>
  <div class="login">
    <svg width="13" height="14" viewBox="0 0 13 14"><circle cx="6.5" cy="4" r="3.5" fill="#bbb"/><path d="M0 14c0-4 3-6 6.5-6S13 10 13 14z" fill="#bbb"/></svg>Login
  </div>
  <div class="btn signup">Sign up</div>
  <svg class="abs" style="left:1010px;top:22px" width="26" height="26" viewBox="0 0 26 26"><circle cx="11" cy="11" r="8.5" fill="none" stroke="#222" stroke-width="2"/><path d="M17 17l7 7" stroke="#222" stroke-width="2"/></svg>
  <svg class="abs" style="left:1053px;top:16px" width="34" height="36" viewBox="0 0 34 36"><path d="M2 10h5l4 16h16l3-12H9" fill="none" stroke="#222" stroke-width="2"/><circle cx="13" cy="31" r="2.2" fill="#222"/><circle cx="25" cy="31" r="2.2" fill="#222"/><circle cx="29" cy="7" r="6" fill="var(--green)"/><text x="29" y="10" font-size="9" fill="#fff" text-anchor="middle" font-family="Lato">1</text></svg>
</header>

<section class="hero">
  <div class="ph" role="img" aria-label="Radish illustration" style="left:372px;top:76px;width:80px;height:90px;background:linear-gradient(160deg,#cfe0c2,#ecd3d6)"></div>
  <div class="ph" role="img" aria-label="Red capsicum illustration" style="left:400px;top:338px;width:58px;height:70px;background:linear-gradient(180deg,#e8c2c0,#e3aeae)"></div>
  <div class="ph" role="img" aria-label="Celery illustration" style="left:122px;top:380px;width:105px;height:90px;background:linear-gradient(135deg,#d6e6cb,#c5dcb6)"></div>
  <div class="ph" role="img" aria-label="Spring onion illustration" style="left:988px;top:390px;width:152px;height:100px;background:linear-gradient(150deg,#cfe2c4,#eef3e6)"></div>
  <div class="ph" role="img" aria-label="Plate of spaghetti bolognese with parmesan" style="left:613px;top:56px;width:440px;height:440px;background:linear-gradient(160deg,#f6f5f3,#e9dfd2)"></div>

  <svg class="abs" style="left:0;top:0" width="1200" height="603">
    <g fill="none" stroke="#555" stroke-width="1.3" stroke-dasharray="3 4">
      <path d="M624 96c20 10 30 -5 50 8s20 0 40 6"/>
      <path d="M980 94c10-20 20-8 30-20s20-6 30-12"/>
      <path d="M1050 230c10-20 20-5 30-18s10-10 20-10"/>
      <path d="M563 430c20 10 30-10 45-5s20-20 40-20"/>
    </g>
  </svg>
  <div class="badge" style="left:556px;top:78px;width:68px;height:68px;background:var(--navy)">Garbs<span>25g</span></div>
  <div class="badge" style="left:1046px;top:36px;width:68px;height:68px;background:var(--teal)">Calories<span>180</span></div>
  <div class="badge" style="left:1101px;top:181px;width:68px;height:68px;background:var(--red)">Fats<span>3g</span></div>
  <div class="badge" style="left:495px;top:395px;width:68px;height:68px;background:var(--teal)">Protein<span>12g</span></div>

  <h1 class="abs wide hero-title">Kids Meals</h1>
  <div class="abs hero-sub">HEALTHY MEALS FOOD IN MARLOW CREEK</div>
  <div class="btn hero-btn">See MENU &amp; Order</div>
  <div class="abs dots"><span></span><span></span><span></span><span class="on"></span></div>
  <svg class="abs" style="left:589px;top:497px" width="22" height="30" viewBox="0 0 22 30"><rect x="2" y="1" width="18" height="28" rx="9" fill="none" stroke="var(--blue)" stroke-width="1.8"/><line x1="11" y1="7" x2="11" y2="12" stroke="var(--blue)" stroke-width="2"/></svg>
</section>

<section class="abs subscribe">
  <p>Join the Lively Oak Dishes subscription service to get the lowest prices. Cancel anytime.</p>
  <div class="sub-input">Your email</div>
  <div class="btn sub-btn">Join Now</div>
</section>

<h2 class="abs wide section-title" style="top:866px">What's fresh at LOD</h2>
<div class="abs rule" style="left:581px;top:906px"></div>

<article class="card" style="left:110px">
  <div class="ph photo" role="img" aria-label="Sliced chicken with roasted carrots and broccoli" style="background:linear-gradient(120deg,#c98a5c,#e4d6cc,#7a9c64)"></div>
  <h3>LOD Kids 7 Day Meal<br>Plan</h3>
  <div class="price" style="color:var(--blue)">$35</div>
  <div class="btn" style="background:var(--blue)">Join Now</div>
</article>
<article class="card" style="left:356px">
  <div class="ph photo" role="img" aria-label="Spaghetti bolognese with parmesan" style="background:linear-gradient(120deg,#eee9e2,#c98e6c,#eee9e2)"></div>
  <h3>LOD Adult 7 Day<br>Meal Plan</h3>
  <div class="price" style="color:var(--red)">$54</div>
  <div class="btn" style="background:var(--red)">Join Now</div>
</article>
<article class="card" style="left:604px">
  <div class="ph photo" role="img" aria-label="Grilled chicken with broccoli and tomato" style="background:linear-gradient(120deg,#6d9c57,#d99a7e,#6d9c57)"></div>
  <h3>LOD Adult 7 Day<br>Couples Meal Plan</h3>
  <div class="price" style="color:var(--teal)">$108</div>
  <div class="btn" style="background:var(--teal)">Join Now</div>
</article>
<article class="card" style="left:851px">
  <div class="ph photo" role="img" aria-label="Assorted healthy sweets and berry slice" style="background:linear-gradient(120deg,#bf9a5e,#d8cbb8,#7a3b4c)"></div>
  <h3>LOD Adult 21 Meals<br>Per Week Plan</h3>
  <div class="price" style="color:var(--green)">$162</div>
  <div class="btn" style="background:var(--green)">Join Now</div>
</article>

<section class="abs ordering" role="img" aria-label="Background photo of a wrapped sandwich">
  <h2 class="wide">New! Online Ordering</h2>
  <p>Online ordering NOW enabled for pick-up or delivery. Just tell us what you want and we'll prepare it as fast as we can. All orders are manually confirmed by us directly. Find out in real-time when your food is ready. All orders are manually confirmed by us in real-time. Watch on-screen when your food is ready for pickup or when it gets delivered.</p>
  <div class="btn">See MENU &amp; Order</div>
</section>

<section class="abs how">
  <div class="abs" style="left:0;width:1200px;top:66px;text-align:center;font-weight:700;font-size:26px;color:var(--ink)">LOD</div>
  <h2 class="abs wide section-title" style="top:112px">How it works</h2>
  <div class="abs" style="left:0;width:1200px;top:150px;text-align:center;font-family:Montserrat,sans-serif;font-size:19px;color:var(--blue)">Easy 3 steps Order</div>

  <svg class="abs" style="left:0;top:0" width="1200" height="400">
    <defs><marker id="arw" markerWidth="10" markerHeight="10" refX="6" refY="5" orient="auto"><path d="M0 0L7 5L0 10" fill="none" stroke="#333" stroke-width="1.4"/></marker></defs>
    <g fill="none" stroke="#333" stroke-width="1.6" stroke-dasharray="5 5">
      <path d="M298 214c30 0 40-22 60-8s-16 30-14 8 50-10 70 12 38 14 56-6 -4-30-14-8 30 28 64 38" marker-end="url(#arw)"/>
      <path d="M672 286c30 0 40-10 52-24s-20-16-12 8 60-34 100-32 0 40-10 22 60-40 82-48" marker-end="url(#arw)"/>
    </g>
  </svg>

  <div class="step">
    <div class="step-ring" style="left:177px;top:153px"></div>
    <svg class="abs" style="left:210px;top:183px" width="46" height="50" viewBox="0 0 46 50" fill="none" stroke="var(--green)" stroke-width="1.6"><rect x="16" y="2" width="26" height="34"/><path d="M21 10h16M21 16h16M21 22h10"/><path d="M2 40a16 12 0 0 1 32 0z"/><path d="M0 44h36"/></svg>
    <div class="step-num" style="left:186px;top:152px">1</div>
    <h4 style="left:83px;top:289px">Select Your Meal Plan</h4>
    <p style="left:83px;top:321px">Lorem consectetur iscing elit, sed do eiusmod tempor incididunt</p>
  </div>
  <div class="step">
    <div class="step-ring" style="left:548px;top:237px"></div>
    <svg class="abs" style="left:584px;top:264px" width="40" height="56" viewBox="0 0 40 56" fill="none" stroke="var(--green)" stroke-width="1.6"><path d="M4 14h32l-2 40H6z"/><path d="M13 14a7 8 0 0 1 14 0"/><path d="M14 26l12 14M26 26L14 40"/></svg>
    <div class="step-num" style="left:557px;top:236px">2</div>
    <h4 style="left:454px;top:373px">Convenient delivery options</h4>
    <p style="left:454px;top:405px">Lorem consectetur iscing elit, sed do eiusmod tempor incididunt</p>
  </div>
  <div class="step">
    <div class="step-ring" style="left:908px;top:153px"></div>
    <svg class="abs" style="left:936px;top:180px" width="56" height="56" viewBox="0 0 56 56" fill="none" stroke="var(--green)" stroke-width="1.6"><path d="M14 4v16M10 4v10a4 4 0 0 0 8 0V4"/><path d="M30 4c-4 0-5 8-5 14h5V4z"/><path d="M4 44a24 14 0 0 1 48 0z"/><circle cx="38" cy="34" r="6"/><path d="M2 48h52"/></svg>
    <div class="step-num" style="left:917px;top:152px">3</div>
    <h4 style="left:814px;top:289px">Fuel when you want</h4>
    <p style="left:814px;top:321px">Lorem consectetur iscing elit, sed do eiusmod tempor incididunt</p>
  </div>
</section>

<section class="smoothie">
  <div class="ph" role="img" aria-label="Green smoothie glass with kiwi" style="left:1064px;top:2224px;width:96px;height:122px;background:linear-gradient(180deg,#e4f0d2,#cfe5b0)"></div>
  <div class="abs smoothie-brand"><span class="dot"></span>Lively Oak Dishes</div>
  <h2 class="wide">The best green smoothie<br>to start your day</h2>
  <p style="top:2494px">The King of Green Smoothies would have to be my Superfood Green Smoothie which contains all the elements necessary for unbelievable muscle growth!!! In order to strip off the fat, add lean muscle mass &amp; to provide your body with all the best vitamins &amp; minerals try the following recipe.</p>
  <p style="top:2636px">Once you have mixed it up sit back and read on to discover why this green smoothie is going to help you achieve your goals..... Handful of Ice 1 Banana 1 Handful of Organic Kale 1/3 Lemon 3 Dates 1/4 Cup of Water (Or Cocunut Water to make it sweet) 1 1/2 scoops of 100% Whey Protein Powder (Sugar Free is important!!See Supliment</p>
  <div class="btn" style="left:111px;top:2815px;width:177px;height:46px;background:var(--green)">Learn More</div>
  <div class="ph" role="img" aria-label="Pea pods illustration" style="left:752px;top:2476px;width:84px;height:70px;background:linear-gradient(135deg,#d5e6c8,#c0d8ae)"></div>
  <div class="ph" role="img" aria-label="Carrot illustration" style="left:1054px;top:2384px;width:112px;height:104px;background:linear-gradient(225deg,#d8e6cb,#f3d2b8)"></div>
  <div class="ph" role="img" aria-label="Woman on an exercise bike holding a green smoothie" style="left:692px;top:2372px;width:410px;height:574px;background:linear-gradient(180deg,#f1ebe6,#cfc6c0 55%,#8e8a88)"></div>
</section>

<footer class="abs site-footer">
  <div class="abs" style="left:111px;top:54px;font-weight:700;font-size:48px;color:#fff;letter-spacing:2px">LOD</div>
  <div class="social" style="left:112px;top:135px" aria-label="Social profile"></div>
  <div class="social" style="left:158px;top:135px" aria-label="Social profile"></div>

  <h5 style="left:404px;top:58px">QUICK LINKS</h5>
  <ul style="left:404px;top:86px"><li>Our menu</li><li>About us</li><li>Blog</li><li>Contacts us</li></ul>

  <h5 style="left:603px;top:58px">CONTACT US</h5>
  <ul style="left:603px;top:86px">
    <li><svg width="10" height="13" viewBox="0 0 10 13"><path d="M5 0a5 5 0 0 0-5 5c0 4 5 8 5 8s5-4 5-8a5 5 0 0 0-5-5z" fill="#fff"/><circle cx="5" cy="5" r="1.8" fill="#1b1b1b"/></svg> Shop 9 – 42 Fernhill Road,</li>
    <li style="padding-left:11px">Marlow Creek, QLD, 4599</li>
    <li><svg width="12" height="12" viewBox="0 0 12 12"><path d="M2 0l3 3-1.5 2a7 7 0 0 0 3.5 3.5L9 7l3 3-2 2C5 12 0 7 0 2z" fill="#fff"/></svg> 0400 000 123</li>
    <li><svg width="14" height="11" viewBox="0 0 14 11"><rect x="1" y="1" width="12" height="9" fill="none" stroke="#fff" stroke-width="1.4"/><path d="M1 1l6 5 6-5" fill="none" stroke="#fff" stroke-width="1.4"/></svg> hello@livelyoakdishes.example</li>
  </ul>

  <h5 style="left:928px;top:58px">OPENING HOURS</h5>
  <ul style="left:928px;top:86px"><li>Mon- Friday – 9 – 5 pm</li><li>Sat – 8 am – 12 pm</li></ul>

  <div class="abs" style="left:111px;top:231px;width:978px;height:1px;background:#444"></div>
  <div class="legal" style="top:252px;font-size:13px">DISCLAIMER &nbsp;|&nbsp; TERMS &nbsp;|&nbsp; CONDITIONS &nbsp;|&nbsp; PRIVACY POLICY</div>
  <div class="legal" style="top:290px">Copyright – 2020 – Lively Oak Dishes Pty Ltd – ABN – 00 000 000 000</div>
</footer>

</body>
</html>
```